Modern Label for cleaning products for the brand Vorlix

We need a label design for our line of cleaning products. The label should feature our logo and an image to identify the product's intended use. I've added our logo and an image for use. This only concerns the design of the label on the front of the bottle.

Label dimensions:
Label 1 (500ml bottle with spray): width 58mm x height 115mm
Label 2: (1L bottle): width 73mm x height 140mm
The design must be consistent for both bottles which you find in the pictures.

The bottles to be labeled are white. See the attachment for a photo of the bottles.

The photo must also appear on the label to identify the product's intended use.

Product information:
Brand: Vorlix
Product: Sanitary Cleaner

This text must be placed on the label:
"Cleans, descales & freshens. followed with this text: "Ideal for quick and powerful cleaning. A ready-to-use product for everyday use."

- Mention the seperate USP's: Sanitary, Bathroom, Toilet, Wet areas

Appearance: This is a consumer product, but it must have a professional appearance. We would like to see a design that use the color blue from our logo.

Target Market(s)

Consumers who take care of their homes and want to maintain it the correct (professional) way

Font styles to use
Sans Serif

Colors
0054AA
0677BA
7BADD7
CADEEF
E8F1F8

Requirements
Must have
• USP's + use of image and logo + blend in 1 design
Nice to have
• Keep the color of the logo in the design
Should not have
• Comic sans

```html
<!DOCTYPE html>
<html lang="en">
<head>
<meta charset="utf-8">
<title>Vorlix Sanitary Cleaner – Front Label</title>
<link rel="stylesheet" href="https://fonts.googleapis.com/css2?family=Poppins:ital,wght@0,400;0,600;0,700;0,800;1,700&family=Montserrat:wght@400;500&display=swap">
<style>
  :root {
    --navy: #0a3477;
    --royal: #0054aa;
    --ocean: #0677ba;
    --sky: #1f9ad8;
    --cyan: #3fc6f2;
    --mist: #7badd7;
    --ice: #cadeef;
    --frost: #e8f1f8;
    --violet: #2b1b68;
    --white: #ffffff;
    --ink: #0a0a0a;
  }
  * { margin: 0; padding: 0; box-sizing: border-box; }
  html, body { width: 1200px; height: 898px; overflow: hidden; background: var(--white); }
  .canvas { position: relative; width: 1200px; height: 898px; background: var(--white); }

  .label {
    position: absolute; left: 424px; top: 99px; width: 357px; height: 703px;
    border-radius: 14px; overflow: hidden; background: var(--white);
    font-family: "Poppins", sans-serif; color: var(--white);
  }
  .label-bg { position: absolute; inset: 0; width: 357px; height: 703px; }

  .tagline {
    position: absolute; left: 252px; top: 17px; width: 90px;
    font-family: "Montserrat", sans-serif; font-size: 9.4px; line-height: 9.6px; font-weight: 500;
  }
  .tagline .accent { color: var(--cyan); font-family: "Poppins", sans-serif; font-weight: 600; }

  .brand-dot {
    position: absolute; left: 127px; top: 40px; width: 106px; height: 106px; border-radius: 50%;
    background: radial-gradient(circle at 45% 40%, var(--white) 0%, var(--frost) 55%, var(--ice) 100%);
    border: 12px solid var(--ocean); box-shadow: 0 0 0 3px var(--white);
  }
  .brand-name {
    position: absolute; left: 0; width: 357px; top: 156px; text-align: center;
    font-size: 44px; font-weight: 800; color: var(--ink); letter-spacing: -1px; line-height: 50px;
  }

  .banner { position: absolute; left: 0; top: 220px; width: 357px; height: 135px; }
  .title-top {
    position: absolute; left: 0; width: 357px; top: 241px; text-align: center; padding-left: 10px;
    font-size: 31px; font-weight: 700; line-height: 34px;
  }
  .title-main {
    position: absolute; left: 0; width: 357px; top: 257px; text-align: center;
    font-size: 67px; font-weight: 700; line-height: 72px; letter-spacing: -1px;
  }
  .title-sub {
    position: absolute; left: 0; width: 357px; top: 314px; text-align: center;
    font-family: "Montserrat", sans-serif; font-size: 11px; font-weight: 400;
  }

  .suitable {
    position: absolute; left: 47px; top: 337px; width: 152px; height: 58px;
    background: var(--ocean); border-radius: 0 0 5px 5px;
  }
  .suitable-tab {
    position: absolute; left: 0; top: 0; width: 75px; height: 17px; background: var(--cyan);
    border-radius: 0 0 5px 0; font-family: "Montserrat", sans-serif; font-size: 7px; line-height: 17px;
    padding-left: 7px;
  }
  .suitable-grid {
    position: absolute; left: 0; top: 18px; width: 152px; height: 40px;
    display: grid; grid-template-columns: 69px 83px; grid-template-rows: 20px 20px;
  }
  .use {
    display: flex; align-items: center; gap: 5px; padding-left: 13px; font-size: 8.6px;
    border-bottom: 1px solid rgba(255,255,255,.15);
  }
  .use:nth-child(odd) { border-right: 1px solid rgba(255,255,255,.15); }
  .use:nth-child(2), .use:nth-child(4) { padding-left: 9px; }
  .use.italic { font-style: italic; font-weight: 700; padding-left: 12px; }
  .use svg { width: 9px; height: 9px; flex: none; }

  .photo {
    position: absolute; left: 0; top: 419px; width: 357px; height: 226px;
    background:
      linear-gradient(180deg, var(--white) 0%, rgba(255,255,255,0) 22%, rgba(255,255,255,0) 70%, var(--ocean) 100%),
      linear-gradient(90deg, #7d7b78 0%, #9c9994 28%, #dcdcdc 48%, #eeeeee 70%, #cfcfcf 100%);
  }

  .footer {
    position: absolute; left: 0; top: 638px; width: 357px; height: 65px;
    background: linear-gradient(180deg, var(--ocean), #1e76c0);
  }
  .ideal {
    position: absolute; left: 15px; top: 9px; font-family: "Montserrat", sans-serif; font-size: 10px; line-height: 11px;
  }
  .ideal strong {
    display: block; font-family: "Poppins", sans-serif; font-style: italic; font-weight: 700;
    font-size: 10.5px; line-height: 11.5px; margin-top: 1px;
  }
  .netwt {
    position: absolute; right: 20px; top: 8px; text-align: right;
    font-family: "Montserrat", sans-serif; font-size: 10px; line-height: 10px;
  }
  .netwt .volume { display: block; font-size: 29px; line-height: 30px; letter-spacing: -1px; margin-right: -3px; }
</style>
</head>
<body>
<main class="canvas">
  <article class="label">
    <svg class="label-bg" viewBox="0 0 357 703" aria-hidden="true">
      <defs>
        <linearGradient id="skyGrad" x1="0" y1="0" x2="1" y2="1">
          <stop offset="0" stop-color="#0a3a82"/>
          <stop offset="0.45" stop-color="#1b8fd6"/>
          <stop offset="0.75" stop-color="#1d5fae"/>
          <stop offset="1" stop-color="#2b1b68"/>
        </linearGradient>
        <radialGradient id="glow" cx="0.5" cy="0.2" r="0.45">
          <stop offset="0" stop-color="#bfeaff" stop-opacity="0.8"/>
          <stop offset="1" stop-color="#bfeaff" stop-opacity="0"/>
        </radialGradient>
        <linearGradient id="leftGrad" x1="0" y1="0" x2="0" y2="1">
          <stop offset="0" stop-color="#1b8fd6"/>
          <stop offset="1" stop-color="#2b2d8a"/>
        </linearGradient>
      </defs>
      <rect width="357" height="703" fill="url(#skyGrad)"/>
      <rect width="357" height="260" fill="url(#glow)"/>
      <rect x="0" y="250" width="120" height="230" fill="url(#leftGrad)"/>
      <path d="M357 112 C 320 210 230 260 170 300 C 100 345 40 390 0 470 L0 703 L357 703 Z" fill="#f6f8fa"/>
      <path d="M357 112 C 320 210 230 260 170 300 C 100 345 40 390 0 470" fill="none" stroke="#3fc6f2" stroke-width="3"/>
      <circle cx="31" cy="249" r="3" fill="#ffffff"/>
      <circle cx="31" cy="249" r="12" fill="#ffffff" opacity="0.25"/>
    </svg>

    <p class="tagline">A READY-TO-USE<br><span class="accent">PRODUCT FOR<br>EVERYDAY USE</span></p>

    <div class="brand-dot" aria-hidden="true"></div>
    <p class="brand-name">vorlix</p>

    <svg class="banner" viewBox="0 0 357 135" aria-hidden="true">
      <defs>
        <linearGradient id="bannerGrad" x1="0" y1="0" x2="1" y2="0">
          <stop offset="0" stop-color="#1f2f7e"/>
          <stop offset="0.45" stop-color="#0e4f9e"/>
          <stop offset="0.8" stop-color="#3fb6ea"/>
          <stop offset="1" stop-color="#0a3f8e"/>
        </linearGradient>
      </defs>
      <path d="M22 40 C 70 5 170 20 250 25 C 300 28 330 20 339 5 C 345 40 350 85 320 105 C 270 135 150 120 90 120 C 60 120 40 125 28 132 C 8 110 10 65 22 40 Z" fill="url(#bannerGrad)"/>
      <path d="M40 22 C 110 0 200 18 260 18 C 305 18 330 12 339 5" fill="none" stroke="#7badd7" stroke-width="2"/>
    </svg>
    <p class="title-top">Sanitary</p>
    <p class="title-main">Cleaner</p>
    <p class="title-sub">CLEANS, DESCALES &amp; FRESHENS</p>

    <section class="suitable">
      <div class="suitable-tab">SUITABLE FOR</div>
      <div class="suitable-grid">
        <div class="use"><svg viewBox="0 0 10 10"><path d="M2 1h2v4h5v2a3 3 0 0 1-3 2H3v-2a2 2 0 0 1-1-2z" fill="#fff"/></svg>Toilet</div>
        <div class="use"><svg viewBox="0 0 10 10"><path d="M1 9V4a3 3 0 0 1 6 0" fill="none" stroke="#7badd7" stroke-width="1.3"/><path d="M6 5l-1 4M7.5 5v4M9 5l.5 4" stroke="#7badd7" stroke-width=".8"/></svg>Wet Areas</div>
        <div class="use italic"><svg viewBox="0 0 10 10"><path d="M2 0l1 6 4 3H2z" fill="#7badd7"/></svg>Sanitary</div>
        <div class="use"><svg viewBox="0 0 10 10"><path d="M1 1h3v4h5v2H7v2H6V7H3v2H1z" fill="#7badd7"/></svg>Bathroom</div>
      </div>
    </section>

    <div class="photo" role="img" aria-label="Photo of a bright modern bathroom with glass shower, washbasin with mirror, tiled bathtub and towel radiator"></div>

    <footer class="footer">
      <p class="ideal">IDEAL FOR<strong>QUICK AND POWERFUL<br>CLEANING.</strong></p>
      <p class="netwt">NET WT.<span class="volume">500ml</span></p>
    </footer>
  </article>
</main>
</body>
</html>
```